CLEARWAY LEGAL

I'm virtually ready to launch my site, but I have a number of edits and modifications that need to be implemented. More importantly, I'm always looking to improve my site, particularly now that I am making my proverbial "FIRST IMPRESSION." Thus, I'm willing to see if there is someone who can add creativity and perhaps improve what I already have, particularly on the All Important Front Page.

```html
<!DOCTYPE html>
<html lang="en">
<head>
<meta charset="utf-8">
<title>Clearway Legal</title>
<link href="https://fonts.googleapis.com/css2?family=Open+Sans:wght@400;600;700&family=Tinos:wght@400;700&display=swap" rel="stylesheet">
<style>
:root{
  --navy:#1f2a5a;
  --navy-deep:#172049;
  --red:#a3001b;
  --red-soft:#e8a6b4;
  --ink:#2b2f3a;
  --grey:#8a8d99;
  --lav:#efedf7;
  --lav-2:#e3e0f1;
  --dark:#2a2f3d;
  --dark-2:#343a4b;
  --white:#ffffff;
  --star:#f08a24;
}
*{margin:0;padding:0;box-sizing:border-box}
html,body{width:1200px;height:4517px;overflow:hidden}
body{position:relative;font-family:"Open Sans",sans-serif;color:var(--ink);background:var(--white)}
.abs{position:absolute}
.serif{font-family:"Tinos",serif}

/* header */
.top-contact{display:flex;align-items:center;gap:10px;font-size:11px;line-height:1.25;color:var(--ink)}
.top-contact small{display:block;color:var(--grey);font-size:10px}
.dot-icon{width:30px;height:30px;border-radius:50%;background:var(--navy);display:flex;align-items:center;justify-content:center}
.btn-book{left:879px;top:9px;width:184px;height:38px;border-radius:19px;background:var(--navy);color:#fff;font-size:11px;font-weight:700;display:flex;align-items:center;justify-content:center;letter-spacing:.3px}
.nav a{position:absolute;top:83px;font-size:12px;color:var(--ink);text-decoration:none}
.brand-badge{border-radius:50%;background:var(--navy);border:3px solid var(--red);display:flex;align-items:center;justify-content:center;text-align:center;color:#fff;font-weight:700;line-height:1.1}

/* hero */
.hero-photo{left:0;top:120px;width:1200px;height:760px;background:linear-gradient(100deg,#3a3f4e 0%,#5b6170 45%,#7f8592 70%,#4b505d 100%)}
.hero-shade{left:0;top:120px;width:1200px;height:760px;background:linear-gradient(90deg,rgba(20,24,36,.7),rgba(20,24,36,.15))}
.eyebrow{left:81px;top:358px;color:#fff;font-size:23px;font-weight:600;letter-spacing:3px}
.hero-title{left:79px;top:410px;color:#fff;font-size:50px;font-weight:700}
.hero-rule{left:81px;top:490px;width:724px;height:1px;background:rgba(255,255,255,.6)}
.hero-copy{left:82px;top:522px;width:640px;color:#fff;font-size:15px;font-weight:600;line-height:26px}
.btn{height:36px;border-radius:18px;font-size:13px;font-weight:600;display:flex;align-items:center;justify-content:center}
.btn-navy{background:var(--navy-deep);color:#fff}
.btn-white{background:#fff;color:var(--navy)}

/* about */
.kicker{font-family:"Tinos",serif;font-size:16px;color:var(--ink)}
.h-serif{font-family:"Tinos",serif;color:var(--navy);font-weight:400}
.muted{color:var(--grey);font-size:12.5px;line-height:23px}
.quote-block{border-left:2px solid var(--navy);padding-left:15px}
.btn-red{background:var(--red);color:#fff;font-size:15px;font-weight:700;display:flex;align-items:center;justify-content:center;gap:16px;border-radius:3px}

/* services */
.band-lav{left:0;width:1200px;background:var(--lav)}
.sec-title{width:1200px;text-align:center;font-family:"Tinos",serif;font-size:46px;color:var(--navy)}
.sec-sub{width:1200px;text-align:center;color:var(--grey);font-size:12.5px;line-height:22px}
.svc-card{top:1749px;width:319px;height:268px;border-radius:4px;overflow:hidden}
.svc-card h3{position:absolute;left:20px;top:56px;color:#fff;font-family:"Tinos",serif;font-size:32px;font-weight:700}
.svc-icon{width:72px;height:72px;border-radius:50%;background:#fff;display:flex;align-items:center;justify-content:center;box-shadow:0 2px 8px rgba(0,0,0,.08)}

.feat{width:280px}
.feat h4{font-family:"Tinos",serif;font-weight:400;font-size:22px;color:var(--navy);margin-bottom:8px}
.feat p{color:var(--grey);font-size:12.5px;line-height:23px}
.feat.left{text-align:right}
.ring{width:88px;height:88px;border-radius:50%;background:#fff;border:2px solid var(--red-soft);display:flex;align-items:center;justify-content:center}
.ring span{width:72px;height:72px;border-radius:50%;background:var(--navy);display:flex;align-items:center;justify-content:center}

/* appointment */
.appt-photo{left:0;top:2815px;width:1200px;height:560px;background:linear-gradient(90deg,#2d3140 0%,#4a4f5e 55%,#6d7280 100%)}
.appt-shade{left:0;top:2815px;width:1200px;height:560px;background:rgba(30,33,45,.55)}
.hours{left:100px;top:3013px;width:454px;height:232px;background:rgba(40,44,58,.75);border-left:4px solid var(--red)}
.hours .row{position:absolute;left:30px;right:8px;height:51px;display:flex;justify-content:space-between;align-items:center;border-bottom:1px solid rgba(255,255,255,.12);font-size:14px}
.hours .row b{color:#fff;font-weight:600}
.hours .row span{color:#9ea2ad}
.form-panel{left:612px;top:2842px;width:490px;height:499px;background:#f3f2f8}
.field{position:absolute;height:52px;background:#fff;border:1px solid #e4e3ec;font-size:13px;color:#8a8d99;display:flex;align-items:center;padding-left:26px}
.btn-submit{position:absolute;left:55px;top:424px;width:384px;height:53px;background:var(--red);color:#fff;font-weight:700;font-size:18px;display:flex;align-items:center;justify-content:center}

/* testimonials */
.t-card{top:3652px;width:323px;height:265px;background:#fff;border-radius:4px;box-shadow:0 3px 14px rgba(31,42,90,.06)}
.t-card .av{position:absolute;left:32px;top:-34px;width:60px;height:60px;border-radius:50%;background:linear-gradient(#cfd2da,#9aa0ad);border:3px solid #fff}
.t-card .q{position:absolute;right:36px;top:-22px;font-family:"Tinos",serif;font-size:90px;line-height:1;font-weight:700}
.t-card .stars{position:absolute;left:28px;top:54px;color:var(--star);font-size:15px;letter-spacing:3px}
.t-card p{position:absolute;left:28px;top:84px;width:275px;color:var(--grey);font-size:12.5px;line-height:23px}
.t-card h5{position:absolute;left:28px;top:188px;font-family:"Tinos",serif;font-weight:400;font-size:21px;color:var(--navy)}
.t-card small{position:absolute;left:28px;top:218px;font-size:9px;color:var(--grey);letter-spacing:.4px}

/* footer */
.fnav a{position:absolute;top:4281px;color:#fff;font-size:13px;font-weight:600;text-decoration:none}
.fcontact{display:flex;align-items:center;gap:16px;color:#fff;font-size:11px;font-weight:600;line-height:17px}
.fcontact .ic{width:56px;height:56px;border-radius:50%;border:1px solid rgba(255,255,255,.5);display:flex;align-items:center;justify-content:center}
.fdiv{top:4370px;width:1px;height:62px;background:rgba(255,255,255,.35)}
.bottom-bar{left:0;top:4464px;width:1200px;height:53px;background:#3a4054}
.social{width:25px;height:25px;border:1.5px solid #fff;border-radius:3px}
</style>
</head>
<body>

<!-- header -->
<div class="abs top-contact" style="left:122px;top:15px">
  <div class="dot-icon"><svg width="14" height="14" viewBox="0 0 24 24"><path fill="#fff" d="M6.6 10.8a15 15 0 0 0 6.6 6.6l2.2-2.2a1 1 0 0 1 1-.25 11.4 11.4 0 0 0 3.6.57 1 1 0 0 1 1 1V20a1 1 0 0 1-1 1A17 17 0 0 1 3 4a1 1 0 0 1 1-1h3.5a1 1 0 0 1 1 1c0 1.25.2 2.45.57 3.6a1 1 0 0 1-.25 1z"/></svg></div>
  <div>Call Us:<small>(123) 456 7890</small></div>
</div>
<div class="abs top-contact" style="left:280px;top:15px">
  <div class="dot-icon"><svg width="14" height="14" viewBox="0 0 24 24"><path fill="#fff" d="M3 5h18v14H3z"/><path d="M3 5l9 7 9-7" fill="none" stroke="#1f2a5a" stroke-width="2"/></svg></div>
  <div>Email:<small>office@company.com</small></div>
</div>
<div class="abs btn-book">BOOK APPOINTMENT</div>
<div class="abs" style="left:700px;top:65px;width:363px;height:1px;background:#ccd"></div>
<nav class="nav">
  <a style="left:123px">Home</a><a style="left:237px">About Us</a><a style="left:386px">Services</a>
  <a style="left:705px">Team</a><a style="left:831px">Blog</a><a style="left:956px">Contact Us</a>
</nav>
<div class="abs brand-badge" style="left:541px;top:23px;width:80px;height:80px;font-size:11px">CLEARWAY<br>LEGAL</div>

<!-- hero -->
<div class="abs hero-photo" role="img" aria-label="Photo of a legal team working together in a bright office"></div>
<div class="abs hero-shade"></div>
<svg class="abs" style="left:0;top:700px" width="1200" height="230" viewBox="0 700 1200 230">
  <path d="M0 772 Q600 982 1200 772 L1200 930 L0 930 Z" fill="#fff"/>
  <path d="M233 855 Q602 925 965 850" fill="none" stroke="var(--red)" stroke-width="4"/>
</svg>
<div class="abs brand-badge" style="left:580px;top:866px;width:44px;height:44px;font-size:6px">CLEARWAY<br>LEGAL</div>
<div class="abs eyebrow">LEGAL SERVICES</div>
<h1 class="abs hero-title">Legal Precision, Client Success</h1>
<div class="abs hero-rule"></div>
<p class="abs hero-copy">Lorem ipsum dolor sit amet, consectetur adipiscing elit et dolore conser tempor incididunt ut labore et dolore magna</p>
<div class="abs btn btn-navy" style="left:82px;top:610px;width:148px">LEARN MORE</div>
<div class="abs btn btn-white" style="left:239px;top:610px;width:180px">REQUEST QUOTE</div>

<!-- about -->
<svg class="abs" style="left:80px;top:950px" width="480" height="480" viewBox="0 0 480 480">
  <path d="M6 225 A225 225 0 0 1 470 240 A225 225 0 0 1 240 470" fill="none" stroke="var(--navy)" stroke-width="7"/>
</svg>
<div class="abs" role="img" aria-label="Portrait of a smiling lawyer in a dark suit with arms crossed" style="left:93px;top:980px;width:450px;height:450px;border-radius:50%;background:radial-gradient(circle at 50% 40%,#d9dde6,#8f96a6)"></div>
<div class="abs kicker" style="left:621px;top:978px">Strength in Legal Protection</div>
<h2 class="abs h-serif" style="left:620px;top:1005px;font-size:46px;line-height:54px;width:540px">Turning Challenges into Legal Triumphs</h2>
<div class="abs quote-block muted" style="left:621px;top:1132px;width:470px">Lorem ipsum dolor sit amet, consectetur adipiscing elit, sed do eiusmod<br>or incididunt ut labore et dolore</div>
<p class="abs muted" style="left:621px;top:1213px;width:470px">Lorem ipsum dolor sit amet, consectetur adipiscing elit, sed do eiusmod tem por incididunt ut labore et dolore magna aliqua. Ut enim ad minim veniam, quis nostrud exercitation ullamco laboris nisi ut aliquip ex ea commodo consequat. Duis aute irure dolor in reprehenderit in voluptate velit esse cillum dolore eu fugiat nulla pariatur. Excepteur</p>
<div class="abs btn-red" style="left:619px;top:1361px;width:155px;height:46px">Contact us
  <svg width="20" height="14" viewBox="0 0 20 14"><path d="M1 7h17M12 1l6 6-6 6" fill="none" stroke="#fff" stroke-width="2"/></svg></div>

<!-- services cards -->
<div class="abs band-lav" style="top:1512px;height:572px"></div>
<h2 class="abs sec-title" style="left:0;top:1562px">Our Services</h2>
<p class="abs sec-sub" style="left:0;top:1629px">Lorem ipsum dolor sit amet, consectetur adipiscing elit, sed do eiusmod temp<br>or incididunt ut labore et dolore</p>

<div class="abs svc-card" style="left:91px" role="img" aria-label="Photo of a business consultation around a laptop" ><div style="position:absolute;inset:0;background:linear-gradient(160deg,#9aa0ab,#4d5260)"></div><h3>Consultation</h3></div>
<div class="abs svc-card" style="left:439px" role="img" aria-label="Photo of a judge's gavel on a desk"><div style="position:absolute;inset:0;background:linear-gradient(160deg,#5a4538,#1f1813)"></div><h3>Litigation</h3></div>
<div class="abs svc-card" style="left:786px" role="img" aria-label="Photo of a lawyer reviewing claim documents with a client"><div style="position:absolute;inset:0;background:linear-gradient(160deg,#6a7080,#b8bcc6)"></div><h3>Collection Claims</h3></div>
<div class="abs svc-icon" style="left:134px;top:1713px"><svg width="30" height="30" viewBox="0 0 30 30" fill="none" stroke="var(--red)" stroke-width="2.4"><circle cx="20" cy="6" r="3"/><path d="M20 10v16M14 26V14M8 26v-8M2 26v-4"/></svg></div>
<div class="abs svc-icon" style="left:482px;top:1713px"><svg width="30" height="30" viewBox="0 0 30 30" fill="none" stroke="var(--red)" stroke-width="2"><circle cx="15" cy="15" r="11"/><circle cx="15" cy="15" r="6"/><circle cx="15" cy="15" r="2" fill="var(--red)"/></svg></div>
<div class="abs svc-icon" style="left:829px;top:1713px"><svg width="30" height="30" viewBox="0 0 30 30" fill="none" stroke="var(--red)" stroke-width="2.4"><path d="M12 16V6a3 3 0 0 1 6 0v8l4 2v6l-4 5h-6l-4-7z"/></svg></div>

<!-- services features -->
<h2 class="abs sec-title" style="left:9px;top:2137px">Our Services</h2>
<p class="abs sec-sub" style="left:12px;top:2204px">Lorem ipsum dolor sit amet, consectetur adipiscing elit, sed do eiusmod temp<br>or incididunt ut labore et dolore</p>
<div class="abs" style="left:340px;top:2320px;width:270px;height:430px;border-radius:50%;background:var(--lav)"></div>
<div class="abs" style="left:600px;top:2320px;width:270px;height:430px;border-radius:50%;background:var(--lav)"></div>
<div class="abs" role="img" aria-label="Portrait of a smiling lawyer with glasses and a grey suit" style="left:440px;top:2340px;width:312px;height:340px;border-radius:50%;background:radial-gradient(circle at 50% 35%,#7f86a8,#2f3a72)"></div>

<div class="abs feat left" style="left:95px;top:2359px"><h4>Client Centric</h4><p>Lorem ipsum dolor sit amet, consectet ur adipiscing elit et dolore conser</p></div>
<div class="abs feat left" style="left:95px;top:2491px"><h4>Free Consultation</h4><p>Lorem ipsum dolor sit amet, consectet ur adipiscing elit et dolore conser</p></div>
<div class="abs feat left" style="left:95px;top:2624px"><h4>Minimize Exposure</h4><p>Lorem ipsum dolor sit amet, consectet ur adipiscing elit et dolore conser</p></div>
<div class="abs feat" style="left:796px;top:2359px"><h4>Attorney Letters</h4><p>Lorem ipsum dolor sit amet, consectet ur adipiscing elit et dolore conser</p></div>
<div class="abs feat" style="left:796px;top:2491px"><h4>Affordable</h4><p>Lorem ipsum dolor sit amet, consectet ur adipiscing elit et dolore conser</p></div>
<div class="abs feat" style="left:796px;top:2624px"><h4>Legal Experts</h4><p>Lorem ipsum dolor sit amet, consectet ur adipiscing elit et dolore conser</p></div>

<div class="abs ring" style="left:396px;top:2359px"><span><svg width="28" height="28" viewBox="0 0 28 28" fill="none" stroke="#fff" stroke-width="2.2"><circle cx="14" cy="5" r="2.5"/><path d="M4 11h20M14 9v8l-5 8M14 17l5 8"/></svg></span></div>
<div class="abs ring" style="left:396px;top:2491px"><span><svg width="28" height="28" viewBox="0 0 28 28" fill="none" stroke="#fff" stroke-width="2.4" stroke-dasharray="3 3"><circle cx="14" cy="14" r="10"/></svg></span></div>
<div class="abs ring" style="left:396px;top:2622px"><span><svg width="28" height="28" viewBox="0 0 28 28" fill="none" stroke="#fff" stroke-width="2.2"><path d="M5 15a9 9 0 0 1 18 0"/><path d="M5 15h18v3H5z"/><path d="M10 22h8"/></svg></span></div>
<div class="abs ring" style="left:691px;top:2359px"><span><svg width="28" height="28" viewBox="0 0 28 28" fill="none" stroke="#fff" stroke-width="2"><circle cx="14" cy="14" r="10"/><circle cx="14" cy="14" r="5"/><circle cx="14" cy="14" r="1.5" fill="#fff"/></svg></span></div>
<div class="abs ring" style="left:691px;top:2491px"><span><svg width="28" height="28" viewBox="0 0 28 28" fill="none" stroke="#fff" stroke-width="2.2"><path d="M5 15a9 9 0 0 1 18 0"/><path d="M5 15h18v3H5z"/><path d="M10 22h8"/></svg></span></div>
<div class="abs ring" style="left:691px;top:2622px"><span><svg width="28" height="28" viewBox="0 0 28 28" fill="none" stroke="#fff" stroke-width="2.2"><rect x="4" y="5" width="6" height="6"/><rect x="18" y="5" width="6" height="6"/><rect x="4" y="17" width="6" height="6"/><rect x="18" y="17" width="6" height="6"/><path d="M10 8h8M10 20h8"/></svg></span></div>

<!-- appointment -->
<div class="abs appt-photo" role="img" aria-label="Photo of lawyers meeting in a conference room"></div>
<div class="abs appt-shade"></div>
<h3 class="abs serif" style="left:93px;top:2950px;color:#fff;font-size:28px;font-weight:400">Opening Hours</h3>
<div class="abs hours">
  <div class="row" style="top:14px"><b>Monday - Friday</b><span>08am - 05pm</span></div>
  <div class="row" style="top:65px"><b>Saturday</b><span>08am - 05pm</span></div>
  <div class="row" style="top:116px"><b>Telephone</b><span>+123 456 7890</span></div>
  <div class="row" style="top:167px;border:none"><b>Email</b><span>info@company.com</span></div>
</div>
<div class="abs form-panel">
  <div class="abs" style="left:55px;top:40px;width:54px;height:54px;border-radius:50%;background:var(--navy);display:flex;align-items:center;justify-content:center"><svg width="26" height="22" viewBox="0 0 26 22" fill="none" stroke="#fff" stroke-width="1.8"><rect x="2" y="5" width="22" height="15"/><path d="M2 5l11 8 11-8"/></svg></div>
  <div class="abs" style="left:121px;top:39px;font-size:13px;font-weight:600;color:var(--navy)">Get in touch with us for more information</div>
  <div class="abs serif" style="left:121px;top:62px;font-size:34px;color:var(--navy)">Make Appointment</div>
  <div class="field" style="left:55px;top:135px;width:182px">First Name</div>
  <div class="field" style="left:254px;top:135px;width:185px">Last Name</div>
  <div class="field" style="left:55px;top:207px;width:182px">Email Address</div>
  <div class="field" style="left:254px;top:207px;width:185px">Phone Number</div>
  <div class="field" style="left:55px;top:278px;width:384px;height:55px">Select Subject</div>
  <div class="field" style="left:55px;top:350px;width:384px;height:55px">dd/mm/yyyy</div>
  <div class="btn-submit">SUBMIT</div>
</div>

<!-- testimonials -->
<div class="abs band-lav" style="top:3375px;height:700px;background:#f6f5fa"></div>
<h2 class="abs sec-title" style="left:0;top:3456px">Our Services</h2>
<p class="abs sec-sub" style="left:0;top:3523px">Lorem ipsum dolor sit amet, consectetur adipiscing elit, sed do eiusmod temp<br>or incididunt ut labore et dolore</p>
<div class="abs t-card" style="left:100px">
  <div class="av" role="img" aria-label="Client avatar"></div><div class="q" style="color:#e6b6c6">&rdquo;</div>
  <div class="stars">★★★★★</div>
  <p>Lorem ipsum dolor sit amet, consectetur adipiscing elit, sed do eiusmod tempor inci didunt ut labore et dolore magna aliqua. Ut enim ad minim veniam, quis</p>
  <h5>Tara Redsing</h5><small>BUSINESSMAN</small>
</div>
<div class="abs t-card" style="left:446px;border-bottom:4px solid var(--navy)">
  <div class="av" role="img" aria-label="Client avatar"></div><div class="q" style="color:var(--red)">&rdquo;</div>
  <div class="stars">★★★★★</div>
  <p>Lorem ipsum dolor sit amet, consectetur adipiscing elit, sed do eiusmod tempor inci didunt ut labore et dolore magna aliqua. Ut enim ad minim veniam, quis</p>
  <h5>Tara Redsing</h5><small>BUSINESSMAN</small>
</div>
<div class="abs t-card" style="left:788px">
  <div class="av" role="img" aria-label="Client avatar"></div><div class="q" style="color:#e6b6c6">&rdquo;</div>
  <div class="stars">★★★★★</div>
  <p>Lorem ipsum dolor sit amet, consectetur adipiscing elit, sed do eiusmod tempor inci didunt ut labore et dolore magna aliqua. Ut enim ad minim veniam, quis</p>
  <h5>Tara Redsing</h5><small>BUSINESSMAN</small>
</div>

<!-- footer -->
<svg class="abs" style="left:0;top:3980px" width="1200" height="537" viewBox="0 3980 1200 537">
  <path d="M0 3990 Q600 4150 1200 3990 L1200 4517 L0 4517 Z" fill="var(--dark)"/>
  <path d="M233 4040 Q602 4100 965 4040" fill="none" stroke="var(--red)" stroke-width="4"/>
</svg>
<div class="abs brand-badge" style="left:580px;top:4047px;width:44px;height:44px;font-size:6px">CLEARWAY<br>LEGAL</div>
<div class="abs brand-badge" style="left:551px;top:4152px;width:102px;height:102px;font-size:13px">CLEARWAY<br>LEGAL</div>
<nav class="fnav">
  <a style="left:358px">HOME</a><a style="left:450px">SERVICES</a><a style="left:556px">ABOUT US</a><a style="left:676px">TESTIMONIALS</a><a style="left:826px">BLOG</a>
</nav>
<div class="abs" style="left:140px;top:4333px;width:921px;height:1px;background:rgba(255,255,255,.4)"></div>
<div class="abs fcontact" style="left:170px;top:4375px">
  <div class="ic"><svg width="28" height="28" viewBox="0 0 28 28" fill="none" stroke="#fff" stroke-width="1.5"><circle cx="14" cy="14" r="11"/><path d="M3 14h22M14 3c-5 6-5 16 0 22M14 3c5 6 5 16 0 22"/></svg></div>
  <div>123, Building Name, Street<br>City, State XY 123456</div>
</div>
<div class="abs fdiv" style="left:430px"></div>
<div class="abs fcontact" style="left:504px;top:4375px">
  <div class="ic"><svg width="22" height="26" viewBox="0 0 22 26" fill="none" stroke="#fff" stroke-width="1.6"><rect x="5" y="2" width="12" height="22" rx="2"/><path d="M9 20h4"/></svg></div>
  <div>PHONE<br>(123) 456 7890</div>
</div>
<div class="abs fdiv" style="left:751px"></div>
<div class="abs fcontact" style="left:826px;top:4375px">
  <div class="ic"><svg width="26" height="22" viewBox="0 0 26 22" fill="none" stroke="#fff" stroke-width="1.6"><rect x="2" y="4" width="22" height="15"/><path d="M2 4l11 8 11-8"/></svg></div>
  <div>EMAIL<br>info@company.com</div>
</div>
<div class="abs bottom-bar"></div>
<div class="abs" style="left:153px;top:4482px;color:#fff;font-size:12px;font-weight:600">Clearway Legal</div>
<div class="abs social" style="left:933px;top:4478px"></div>
<div class="abs social" style="left:966px;top:4478px"></div>
<div class="abs social" style="left:1000px;top:4478px"></div>
<div class="abs social" style="left:1033px;top:4478px"></div>

</body>
</html>
```